CREATE A BUSINESS CARD FOR A BOAT CLEANING SERVICE

WE ARE STARTING A NEW BOAT CLEANING BUSINESS. WE DIVE UNDERWATER TO CLEAN BOAT HULLS, JETTIES, UNDERWATER STRUCTURES ETC. WE ARE LOOKING FOR AN UPPERMARKET MODERN LOGO AND BUSINESS CARD AS ALOT OF OUR TARGET MARKET WILL BE HIGH END. YOU HAVE TO DESIGN A BUSINESS CARD AND LOGO SEPERATELY .
THE BUSINESS CARD DIMESNION MUST BE STANDARD SIZE.
The standard dimensions of a printed business card are 3.5 x 2 inches

Target Market(s)

UNDERWATER SERVICED

Industry/Entity Type

Business

Contact Information for Business Card

HOLLAND UNDERWATER SERVICES

Font styles to use
Serif

Colors

Designer to choose colors to be used in the design.

Requirements
Must have
• HOLLAND
Nice to have
• dark
Should not have
• more than 3 colors

```html
<!DOCTYPE html>
<html lang="en">
<head>
<meta charset="utf-8">
<title>Holland Underwater Service – Business Card</title>
<link href="https://fonts.googleapis.com/css2?family=Roboto:wght@300;400;500&display=swap" rel="stylesheet">
<style>
  :root {
    --page: #e9eaec;
    --card-top: #ffffff;
    --card-bottom: #f1f2f4;
    --blue: #1f6fb2;
    --blue-light: #4f9cc9;
    --grey: #b9bcc0;
    --grey-text: #a9adb2;
    --grey-dark: #8d9196;
  }
  * { margin: 0; padding: 0; box-sizing: border-box; }
  html, body { width: 1200px; height: 1023px; overflow: hidden; }
  body {
    background: var(--page);
    font-family: "Roboto", Arial, sans-serif;
    position: relative;
  }
  .card {
    position: absolute;
    left: 100px; top: 226px;
    width: 1000px; height: 571px;
    border-radius: 22px;
    background: linear-gradient(160deg, var(--card-top) 30%, var(--card-bottom) 100%);
    box-shadow: 0 14px 40px rgba(0,0,0,.14), 0 2px 6px rgba(0,0,0,.08);
    overflow: hidden;
  }
  .edge-band { position: absolute; right: 45px; top: 0; width: 40px; height: 571px; }

  .brand { position: absolute; left: 70px; top: 170px; width: 360px; text-align: center; }
  .brand-mark {
    width: 92px; height: 92px; border-radius: 50%;
    background: var(--blue-light); margin: 0 auto 26px;
  }
  .brand-name {
    font-weight: 300; font-size: 46px; letter-spacing: 20px;
    color: var(--blue-light); padding-left: 20px;
  }
  .brand-tagline {
    margin-top: 8px; font-weight: 300; font-size: 20px;
    letter-spacing: 5.5px; color: var(--grey-text);
  }

  .divider { position: absolute; left: 455px; top: 150px; width: 1.5px; height: 290px; background: var(--blue-light); }

  .contact { position: absolute; left: 492px; top: 118px; }
  .contact-name { font-weight: 500; font-size: 38px; color: var(--blue); letter-spacing: 1px; }
  .contact-role { font-weight: 300; font-size: 21px; color: var(--grey-text); margin-top: 2px; }
  .contact-address { font-weight: 300; font-size: 20px; color: var(--grey-text); line-height: 29px; margin-top: 10px; }
  .contact-lines { list-style: none; margin-top: 6px; }
  .contact-lines li {
    display: flex; align-items: center; gap: 12px;
    font-weight: 300; font-size: 20px; color: var(--grey-text); line-height: 30px;
  }
  .contact-lines svg { width: 15px; height: 15px; flex: none; }
  .contact-lines .web-accent { color: var(--blue); font-weight: 400; }

  .badges { position: absolute; left: 500px; top: 455px; display: flex; gap: 26px; align-items: center; }
  .badge { width: 58px; height: 58px; border-radius: 50%; }
  .badge-partner { background: #3b97b0; }
  .badge-member { background: #1d2a33; width: 62px; height: 62px; }
</style>
</head>
<body>
  <article class="card">
    <svg class="edge-band" viewBox="0 0 40 571" aria-hidden="true">
      <polygon points="0,0 40,0 40,228 0,246" fill="var(--blue)"/>
      <polygon points="0,258 40,240 40,571 0,571" fill="var(--grey)"/>
    </svg>

    <div class="brand">
      <div class="brand-mark"></div>
      <div class="brand-name">HOLLAND</div>
      <div class="brand-tagline">UNDERWATER SERVICE</div>
    </div>

    <div class="divider"></div>

    <div class="contact">
      <h1 class="contact-name">MARCUS REED</h1>
      <p class="contact-role">President</p>
      <p class="contact-address">410, 88 Harbour Rd, SW<br>Westport, NS B0V 1H0</p>
      <ul class="contact-lines">
        <li>
          <svg viewBox="0 0 16 16"><path d="M4 1.5l2.2 3-1.3 1.6c.8 1.8 2.2 3.2 4 4l1.6-1.3 3 2.2-1.3 2.5C7 13.3 2.7 9 2 3.3z" fill="var(--grey-dark)"/></svg>
          (555) 201-4478
        </li>
        <li>
          <svg viewBox="0 0 16 16"><rect x="1.5" y="3.5" width="13" height="9" fill="none" stroke="var(--grey-dark)" stroke-width="1.4"/><path d="M1.5 3.5L8 9l6.5-5.5" fill="none" stroke="var(--grey-dark)" stroke-width="1.4"/></svg>
          info@hollandunderwater.com
        </li>
        <li>
          <svg viewBox="0 0 16 16"><circle cx="8" cy="8" r="6.3" fill="none" stroke="var(--grey-dark)" stroke-width="1.3"/><ellipse cx="8" cy="8" rx="2.6" ry="6.3" fill="none" stroke="var(--grey-dark)" stroke-width="1.1"/><path d="M1.7 8h12.6" stroke="var(--grey-dark)" stroke-width="1.1"/></svg>
          <span>www.<span class="web-accent">hollandunderwater</span>.com</span>
        </li>
      </ul>
    </div>

    <div class="badges">
      <div class="badge badge-partner"></div>
      <div class="badge badge-member"></div>
    </div>
  </article>
</body>
</html>
```